Communication and Marketing agency needs a new presentation card

We are a group of communication and marketing agencies specialized in companies that are in the logistics and industrial sector. The head agency is TELVANO Grupo and the group consists of 4 agencies: TELVANO Media, TELVANO Digital, TELVANO Research and DifundeEnPantalla. We hace 4 offices in Spain (Madrid, Barcelona, Valencia and Murcia). We are looking for a clean and attractive design that transmits our experience, brand presence in the market and knowledge to those who receive the card.It has to maintain the colors of the logo that is attached.
Target Market(s)
logistics and industrial sector
Marketing department
Contact Information for Business Card
Clean and attractive design

```html
<!DOCTYPE html>
<html lang="es">
<head>
<meta charset="UTF-8">
<title>TELVANO Grupo – Tarjeta de presentación</title>
<link rel="stylesheet" href="https://fonts.googleapis.com/css2?family=Roboto:wght@400;500;700&display=swap">
<style>
  :root {
    --page-bg: #d8d3ce;
    --card-bg: #efeeeb;
    --brand-red: #7d1519;
    --band-dark: #5e0c10;
    --band-light: #8e1a1f;
    --ink: #2b2b2b;
    --ink-soft: #3a3a3a;
    --band-text: #f1e7e7;
    --edge: #c9c6c2;
  }
  * { box-sizing: border-box; margin: 0; padding: 0; }
  html, body {
    width: 1200px; height: 969px; overflow: hidden;
    background: var(--page-bg);
    font-family: "Roboto", Arial, sans-serif;
  }
  .business-card {
    position: absolute; left: 100px; top: 200px;
    width: 1000px; height: 568px;
    background: var(--card-bg);
    border: 1px solid var(--edge);
    box-shadow: 0 14px 40px rgba(0,0,0,.18);
  }
  .brand-name {
    position: absolute; left: 71px; top: 62px;
    color: var(--brand-red);
    font-weight: 500; font-size: 58px; line-height: 1.05; letter-spacing: 1px;
  }
  .brand-name span { display: block; padding-left: 272px; font-size: 40px; }
  .person-name {
    position: absolute; left: 71px; top: 226px;
    color: var(--brand-red); font-weight: 700; font-size: 34px;
  }
  .person-role {
    position: absolute; left: 71px; top: 270px;
    color: var(--ink); font-weight: 500; font-size: 23px;
  }
  .contact-list {
    position: absolute; left: 71px; top: 316px; list-style: none;
  }
  .contact-list li {
    display: flex; align-items: center; gap: 12px;
    height: 32px; font-size: 23px; color: var(--ink-soft);
  }
  .contact-list svg { width: 20px; height: 20px; fill: var(--brand-red); flex: none; }
  .office-list {
    position: absolute; left: 71px; top: 488px;
    font-size: 23px; color: var(--ink-soft);
  }
  .office-list .dot { color: var(--brand-red); margin: 0 6px; }
  .agency-band {
    position: absolute; left: 639px; top: 0; width: 310px; height: 100%;
    background: linear-gradient(160deg, var(--band-light) 0%, var(--band-dark) 60%, var(--band-light) 100%);
    border-left: 3px solid #3e0a0c; border-right: 3px solid #3e0a0c;
  }
  .agency {
    position: absolute; right: 38px; text-align: right;
    color: var(--band-text); font-weight: 400; font-size: 40px; letter-spacing: 1px; line-height: 1;
  }
  .agency small { display: block; font-size: 25px; margin-top: 6px; letter-spacing: 0; }
  .agency--digital { top: 80px; }
  .agency--media { top: 200px; }
  .agency--research { top: 320px; }
  .agency--video { top: 440px; font-size: 30px; line-height: 1.25; }
</style>
</head>
<body>
  <div class="business-card">
    <div class="brand-name">TELVANO<span>Grupo</span></div>

    <div class="person-name">Lorenzo Ibarra</div>
    <div class="person-role">Director</div>

    <ul class="contact-list">
      <li><svg viewBox="0 0 24 24"><path d="M6.6 10.8a15 15 0 0 0 6.6 6.6l2.2-2.2a1 1 0 0 1 1-.25 11.4 11.4 0 0 0 3.6.57 1 1 0 0 1 1 1V20a1 1 0 0 1-1 1A17 17 0 0 1 3 4a1 1 0 0 1 1-1h3.5a1 1 0 0 1 1 1c0 1.25.2 2.45.57 3.6a1 1 0 0 1-.25 1z"/></svg>910 472 318</li>
      <li><svg viewBox="0 0 24 24"><path d="M7 1h10a2 2 0 0 1 2 2v18a2 2 0 0 1-2 2H7a2 2 0 0 1-2-2V3a2 2 0 0 1 2-2zm0 3v14h10V4zm5 15.2a1.2 1.2 0 1 0 0 2.4 1.2 1.2 0 0 0 0-2.4z"/></svg>655 218 740</li>
      <li><svg viewBox="0 0 24 24"><path d="M2 5h20v14H2zm2 2v.5l8 5 8-5V7zm0 2.8V17h16V9.8l-8 5z"/></svg>libarra@telvano.es</li>
      <li><svg viewBox="0 0 24 24"><rect x="2" y="2" width="20" height="20" rx="3"/></svg>lorenzoibarra</li>
      <li><svg viewBox="0 0 24 24"><circle cx="12" cy="12" r="10"/></svg>telvano.es</li>
    </ul>

    <div class="office-list">Madrid<span class="dot">•</span>Barcelona<span class="dot">•</span>Valencia<span class="dot">•</span>Murcia</div>

    <div class="agency-band">
      <div class="agency agency--digital">TELVANO<small>Digital</small></div>
      <div class="agency agency--media">TELVANO<small>Media</small></div>
      <div class="agency agency--research">TELVANO<small>Research</small></div>
      <div class="agency agency--video">DIFUNDE<br>ENPANTALLA</div>
    </div>
  </div>
</body>
</html>
```